Quorva - corporate Business Card

We need a good look and innovative business card for a new start up company based in Los Angeles called "Quorva". We are in a payment business, including payment card, app, and ewallet. We are expert in online payment and Card not present (CNP) transaction.
We need an innovative, modern business card.

Our logo font is Aero Matics

Target Market(s)

Startup - Bank - Online Payment - Card Manufacturing

Industry/Entity Type

Startup

Contact Information for Business Card

phone: 555 014 7396 - Address: 4172 Marlowe blvd, Brenmoor City, OR 97299

Requirements
Must have
• Message: innovative, professional, expert, high tech, trust, online payment expert, security
Nice to have
• no comment
Should not have
• no Comment

```html
<!DOCTYPE html>
<html lang="en">
<head>
<meta charset="utf-8">
<title>Quorva – Business Card</title>
<link href="https://fonts.googleapis.com/css2?family=Lato:wght@400;700&display=swap" rel="stylesheet">
<style>
  :root {
    --brand-red: #b01e2e;
    --ink-dark: #3f3f41;
    --card-dark: #444446;
    --card-white: #ffffff;
    --swoosh-grey: #4a4a4c;
    --backdrop: #d9d9db;
    --url-light: #e6e6e6;
  }
  * { margin: 0; padding: 0; box-sizing: border-box; }
  html, body { width: 1200px; height: 900px; overflow: hidden; }
  body {
    background: var(--backdrop);
    font-family: "Lato", Arial, sans-serif;
    position: relative;
  }
  .card {
    position: absolute;
    left: 337px;
    width: 525px;
    height: 300px;
    overflow: hidden;
    box-shadow: 0 6px 18px rgba(0,0,0,0.18);
  }
  .card--front { top: 110px; background: var(--card-white); }
  .card--back { top: 490px; background: var(--card-dark); }

  .brand { position: absolute; display: flex; align-items: center; gap: 14px; }
  .brand__dot { width: 58px; height: 58px; border-radius: 50%; flex: none; }
  .brand__name { font-weight: 700; letter-spacing: 1px; line-height: 1; }

  .card--front .brand { left: 34px; top: 96px; }
  .card--front .brand__dot { background: var(--brand-red); }
  .card--front .brand__name { color: var(--ink-dark); font-size: 50px; }

  .person { position: absolute; right: 44px; top: 40px; text-align: right; }
  .person__name { color: var(--brand-red); font-size: 17px; font-weight: 700; }
  .person__title { color: var(--ink-dark); font-size: 12px; margin-top: 1px; }

  .address { position: absolute; right: 44px; top: 104px; text-align: right; color: var(--ink-dark); font-size: 12px; line-height: 1.45; }
  .address__label { color: var(--brand-red); font-size: 12px; margin-bottom: 6px; }

  .contacts { position: absolute; left: 30px; top: 200px; color: var(--ink-dark); font-size: 12.5px; line-height: 1.55; }
  .contacts__row { display: flex; align-items: center; gap: 7px; }
  .contacts__icon { width: 11px; height: 11px; fill: var(--brand-red); flex: none; }

  .swoosh { position: absolute; left: 0; bottom: 0; width: 525px; height: 300px; }
  .swoosh__band { fill: var(--brand-red); }
  .swoosh__line { fill: none; stroke: var(--swoosh-grey); stroke-width: 3; }

  .front-url { position: absolute; left: 34px; bottom: 10px; color: var(--card-white); font-size: 12px; }

  .card--back .brand { left: 50%; top: 112px; transform: translateX(-50%); }
  .card--back .brand__dot { background: var(--card-white); width: 64px; height: 64px; }
  .card--back .brand__name { color: var(--card-white); font-size: 56px; }
  .back-url { position: absolute; left: 0; right: 0; top: 200px; text-align: center; color: var(--url-light); font-size: 11px; letter-spacing: 0.5px; }
</style>
</head>
<body>

  <section class="card card--front" aria-label="Business card front">
    <div class="brand">
      <span class="brand__dot"></span>
      <span class="brand__name">quorva</span>
    </div>

    <div class="person">
      <p class="person__name">Daniel Harrow</p>
      <p class="person__title">General Manager</p>
    </div>

    <div class="address">
      <p class="address__label">Address:</p>
      <p>4172 Marlowe blvd</p>
      <p>Brenmoor City, OR 97299</p>
    </div>

    <div class="contacts">
      <p class="contacts__row">
        <svg class="contacts__icon" viewBox="0 0 24 24" aria-hidden="true"><path d="M6.6 10.8a15.1 15.1 0 0 0 6.6 6.6l2.2-2.2c.3-.3.7-.4 1-.2 1.1.4 2.3.6 3.6.6.6 0 1 .4 1 1V20c0 .6-.4 1-1 1C10.6 21 3 13.4 3 4c0-.6.4-1 1-1h3.5c.6 0 1 .4 1 1 0 1.3.2 2.5.6 3.6.1.3 0 .7-.2 1z"/></svg>
        <span>555 014 7396</span>
      </p>
      <p class="contacts__row">
        <svg class="contacts__icon" viewBox="0 0 24 24" aria-hidden="true"><path d="M2 5h20v14H2z M2 5l10 8 10-8"/></svg>
        <span>info@quorva.com</span>
      </p>
    </div>

    <svg class="swoosh" viewBox="0 0 525 300" aria-hidden="true">
      <path class="swoosh__band" d="M0 300 L0 258 C110 252 200 282 300 274 C400 266 465 232 525 212 L525 300 Z"/>
      <path class="swoosh__line" d="M0 251 C110 244 200 274 300 266 C400 258 465 224 525 204"/>
    </svg>
    <p class="front-url">www.quorva.com</p>
  </section>

  <section class="card card--back" aria-label="Business card back">
    <div class="brand">
      <span class="brand__dot"></span>
      <span class="brand__name">quorva</span>
    </div>
    <p class="back-url">www.quorva.com</p>
  </section>

</body>
</html>
```